Coral Wing Flights brochure

A single A4 brochures that is tri-folded and shows some of our tour packages with contact details.

Please visit www.coralwingflights.com.au to see the designs and images that can be used.

I want to provide designers the freedom to try something creative because I want to give prospective client - normally tourists to Sydney a quality service. I want the brochure to reflect this.

The image on the front page needs to be of the Sydney Harbour. The image MUST be in daylight - not night time.

I have now provided an image of the aircraft (in GIF format). Please use this image and place it over the image of the sydney harbour bridge and quayside concert pavilion.

I may need to discuss this further but what I have not show in the attached files is a small form I will like the client to fill out..

Reservation number
Name
Address
Phone number
Email

We can discuss this at a latter time.

The QR Code needs to contain your web address (www.coralwingflights.com.au)

Target Market(s)

Visitors and tourists to Sydney who want a day trip.
We are providing an exciting way to see Sydney. By air in a light aircraft...

Industry/Entity Type

House

Font styles to use
Sans Serif
Script

Colors
33a6d7
3276b5
85acd3
85cae6
ffffff

Requirements
Must have
• Brochure must be A4 (with about 2 to 3mm bleed - so it can be cut at the printers). They but be folded in 3 to produce a DL size brochure.

The words "Prepare to be amazed" should be in script font...

Please use the following wording for our Terms can conditions...

Terms and Conditions
Coral Wing Flights operates from Merrowdale Airfield within Sydney’s busy airspace Your chosen flight may be subject to delays. Clearance to enter controlled airspace may be refused - this is especially true of our popular Coastline Panorama flight. If this happens, we can either offer other suitable flights, reschedule the flight or, if this isn’t suitable, we provide a refund.
Other aircraft, besides our standard Talbin Skyrunners, are available if we consider they better suit your requirements.
See our web site www.coralwingflights.com.au for full details.
Coral Wing Flights is a trading name of Orvexa Pty Limited
(ABN 81 417 286 309) which operates under the Air Operators Certificate (AOC) of Dorrigan and Welsford Pty Ltd.
Nice to have
• Suggestion - on one of the sides (with the packages) to have a background image.

Suggestion is to keep the brochure light and "airy"

```html
<!DOCTYPE html>
<html lang="en">
<head>
<meta charset="utf-8">
<title>Coral Wing Flights – Tour Packages</title>
<link href="https://fonts.googleapis.com/css2?family=Open+Sans:wght@300;400;600;700&display=swap" rel="stylesheet">
<style>
  :root {
    --sky: #33a6d7;
    --deep: #3276b5;
    --soft: #85acd3;
    --pale: #85cae6;
    --white: #ffffff;
    --ink: #111111;
    --text: #222222;
  }
  * { margin: 0; padding: 0; box-sizing: border-box; }
  html, body { width: 1200px; height: 849px; overflow: hidden; background: var(--white); }
  body { font-family: "Open Sans", Arial, sans-serif; color: var(--text); }
  .brochure { position: relative; width: 1200px; height: 849px; overflow: hidden; background: var(--white); }

  .top-band { position: absolute; left: 0; top: 0; width: 1200px; height: 118px; background: var(--sky); }
  .quote {
    position: absolute; top: 20px; width: 400px; padding: 0 10px;
    text-align: center; color: var(--white); font-size: 13.5px; line-height: 23px;
    letter-spacing: -0.2px; white-space: nowrap;
  }
  .quote-mark { color: var(--soft); font-weight: 700; font-size: 26px; line-height: 0; position: relative; top: 7px; font-family: Georgia, serif; }
  .quote-mark.open { margin-right: 8px; }
  .quote-mark.close { margin-left: 6px; }

  .photo { position: absolute; top: 118px; width: 400px; height: 300px; }
  .photo.harbour { left: 0; background: linear-gradient(170deg, #8d9598 0%, #6f8486 30%, #4f7478 55%, #3f6a70 80%, #7a6e66 100%); }
  .photo.coast { left: 400px; background: linear-gradient(180deg, #5d9bd4 0%, #b9d6ee 28%, #6b8a6e 42%, #4c6a55 52%, #1d4a85 65%, #123d78 100%); }
  .photo.mountains { left: 800px; background: linear-gradient(180deg, #8a8fc0 0%, #c9a6b5 22%, #b06a2c 40%, #d08a38 55%, #5d6a2a 75%, #2f4a1e 100%); }

  .title-rule { position: absolute; left: 0; top: 114px; width: 1200px; height: 3px; background: var(--ink); }
  .tour-title {
    position: absolute; top: 100px; height: 30px; padding: 0 16px 0 22px;
    background: var(--ink); color: var(--white);
    font-size: 17px; font-weight: 300; line-height: 30px; white-space: nowrap;
  }

  .wave { position: absolute; left: 0; top: 330px; width: 1200px; height: 110px; }

  .clock { position: absolute; top: 425px; width: 36px; height: 36px; }
  .duration {
    position: absolute; top: 466px; width: 400px; text-align: center;
    color: var(--deep); font-size: 20px; line-height: 26px;
  }

  .stops { position: absolute; list-style: none; }
  .stops li { position: relative; padding-left: 22px; font-size: 14px; line-height: 30px; white-space: nowrap; }
  .stops.wide li { font-size: 15px; }
  .stops li::before {
    content: ""; position: absolute; left: 1px; top: 10px; width: 10px; height: 10px;
    background: var(--ink); transform: rotate(45deg);
  }
  .stops li::after {
    content: ""; position: absolute; left: 4.5px; top: 13.5px; width: 3px; height: 3px;
    background: var(--white); border-radius: 50%;
  }

  .price {
    position: absolute; top: 762px; width: 208px; height: 46px;
    background: var(--deep); color: var(--white);
    font-size: 20px; line-height: 46px; padding-left: 17px;
    clip-path: polygon(0 0, 184px 0, 208px 50%, 184px 100%, 0 100%);
  }

  .bottom-band { position: absolute; left: 0; top: 826px; width: 1200px; height: 23px; background: var(--deep); }
</style>
</head>
<body>
<main class="brochure">
  <div class="top-band"></div>

  <p class="quote" style="left:0"><span class="quote-mark open">&ldquo;</span>This is one of our most popular scenic tours because<br>it showcases Sydneys magnificent coastline and<br>world famous beaches.<span class="quote-mark close">&rdquo;</span></p>
  <p class="quote" style="left:400px"><span class="quote-mark open">&ldquo;</span>This is one of our most popular scenic tours because<br>it showcases Sydneys magnificent coastline and<br>world famous beaches.<span class="quote-mark close">&rdquo;</span></p>
  <p class="quote" style="left:800px"><span class="quote-mark open">&ldquo;</span>This is one of our most popular scenic tours because<br>it showcases Sydneys magnificent coastline and<br>world famous beaches.<span class="quote-mark close">&rdquo;</span></p>

  <div class="photo harbour" role="img" aria-label="Aerial photo of the harbour, city towers and bridge in daylight"></div>
  <div class="photo coast" role="img" aria-label="Photo of sea cliffs and coastline under a blue sky"></div>
  <div class="photo mountains" role="img" aria-label="Photo of sunlit sandstone rock pillars above forested valleys"></div>

  <div class="title-rule"></div>
  <h2 class="tour-title" style="right:800px">Coastline Panorama</h2>
  <h2 class="tour-title" style="right:400px">Sydney Coastal</h2>
  <h2 class="tour-title" style="right:0">The Blue Mountains</h2>

  <svg class="wave" viewBox="0 0 1200 110" preserveAspectRatio="none" aria-hidden="true">
    <path d="M0 48 C250 62 450 80 700 62 C900 48 1050 25 1200 15 L1200 110 L0 110 Z" fill="var(--deep)"/>
    <path d="M0 60 C250 72 450 92 700 76 C900 62 1050 40 1200 32 L1200 110 L0 110 Z" fill="var(--sky)"/>
    <path d="M0 66 C250 78 450 98 700 86 C900 76 1050 55 1200 48 L1200 110 L0 110 Z" fill="var(--pale)"/>
    <path d="M0 72 C250 82 450 96 700 90 C900 84 1050 66 1200 60 L1200 110 L0 110 Z" fill="var(--soft)" opacity="0.6"/>
    <path d="M0 74 C250 84 430 88 640 92 C850 96 1050 94 1200 90 L1200 110 L0 110 Z" fill="var(--white)"/>
  </svg>

  <svg class="clock" style="left:174px" viewBox="0 0 36 36" aria-hidden="true"><circle cx="18" cy="18" r="15.5" fill="none" stroke="var(--deep)" stroke-width="2.5"/><path d="M18 9 V19 H25" fill="none" stroke="var(--deep)" stroke-width="2.5"/></svg>
  <svg class="clock" style="left:569px" viewBox="0 0 36 36" aria-hidden="true"><circle cx="18" cy="18" r="15.5" fill="none" stroke="var(--deep)" stroke-width="2.5"/><path d="M18 9 V19 H25" fill="none" stroke="var(--deep)" stroke-width="2.5"/></svg>
  <svg class="clock" style="left:985px" viewBox="0 0 36 36" aria-hidden="true"><circle cx="18" cy="18" r="15.5" fill="none" stroke="var(--deep)" stroke-width="2.5"/><path d="M18 9 V19 H25" fill="none" stroke="var(--deep)" stroke-width="2.5"/></svg>

  <p class="duration" style="left:-7px">Duration: 1 hour 20 mins</p>
  <p class="duration" style="left:388px">Duration: 1 hour 20 mins</p>
  <p class="duration" style="left:804px">Duration: 1 hour 10 mins</p>

  <ul class="stops wide" style="left:136px;top:510px">
    <li>Parramatta City</li>
    <li>Hornsby</li>
    <li>Bahai Temple</li>
    <li>Sydney Harbour Bridge</li>
    <li>Quayside Concert Pavilion</li>
    <li>Manly</li>
    <li>Long Reef</li>
  </ul>

  <ul class="stops" style="left:526px;top:503px">
    <li>Cambelltown</li>
    <li>Stanwell Park</li>
    <li>Entrance of Port Hacking</li>
    <li>Entrance of Botany Bay</li>
    <li>Famous Sydney Beaches including</li>
    <li>Maroubra, Cooge, Bondi &amp; Manly</li>
    <li>Sydney Heads</li>
    <li>Long Reef</li>
  </ul>

  <ul class="stops" style="left:949px;top:503px">
    <li>Katoomba</li>
    <li>The Three Sisters</li>
    <li>Warragamba Dam</li>
    <li>Prospect Resrvour</li>
  </ul>

  <p class="price" style="left:0">$560 per aircraft</p>
  <p class="price" style="left:400px">$560 per aircraft</p>
  <p class="price" style="left:800px">$475 per aircraft</p>

  <div class="bottom-band"></div>
</main>
</body>
</html>
```